New design for Comparison website

We need new design for our website https://prisvaktposten.no/ . We compare prices and providers in different niches such as electricity, mobile plans, broadband etc.

We would like to see design like Tarivo com or our competitor kjøpklokt no

We will need design of all pages, with tables, tables are somewhat different depending on the service compared (use kjøpklokt no for reference) . Our focus is CTR through comparison Tables.

Final design must communicate following: Professionalism, thrust, authority.

Number of Pages Required

5+ page

Font styles to use
Sans Serif

Colors

Designer to choose colors to be used in the design.

Requirements
Must have
• Tables
Nice to have
• Images in content

```html
<!DOCTYPE html>
<html lang="en">
<head>
<meta charset="utf-8">
<title>Prisvaktposten – Compare providers</title>
<link href="https://fonts.googleapis.com/css2?family=Montserrat:wght@400;500;600;700&family=Arimo:wght@400;700&display=swap" rel="stylesheet">
<style>
:root{
  --green:#0fa67b;
  --green-dark:#0c8f69;
  --charcoal:#4e4e4e;
  --dark:#3a3a3a;
  --text:#555a5f;
  --muted:#8a8f94;
  --line:#e6e8ea;
  --soft:#f4f5f7;
  --white:#ffffff;
}
*{box-sizing:border-box;margin:0;padding:0}
html,body{width:1200px;height:2514px;overflow:hidden}
body{font-family:"Arimo",Arial,sans-serif;color:var(--text);background:var(--white);position:relative}
a{color:inherit;text-decoration:none}

/* Header */
.site-header{position:absolute;left:0;top:0;width:1200px;height:94px;background:var(--white)}
.brand{position:absolute;display:flex;align-items:center;gap:10px;font-family:"Montserrat",Arial,sans-serif;font-weight:700;color:var(--green);white-space:nowrap}
.brand-mark{width:22px;height:22px;background:var(--green)}
.site-header .brand{left:87px;top:27px;font-size:28px}
.lang-select{position:absolute;left:960px;top:23px;width:153px;height:44px;border:1px solid #ccc;border-radius:3px;background:#f3f3f3;display:flex;align-items:center;padding:0 12px;font-size:13px;color:#333;gap:8px}
.lang-select .flag{width:16px;height:10px;background:#2c3e7a}
.lang-select svg{margin-left:auto}

/* Navigation */
.main-nav{position:absolute;left:0;top:94px;width:1200px;height:57px;background:var(--green);border-bottom:3px solid #49c39c}
.main-nav ul{list-style:none;position:absolute;left:87px;top:0;height:54px;display:flex}
.main-nav li{height:54px;display:flex;align-items:center;justify-content:center;font-family:"Montserrat",Arial,sans-serif;font-weight:600;font-size:11px;color:var(--white);white-space:nowrap}
.main-nav li.active{background:#5a5a5a}

/* Hero */
.hero{position:absolute;left:0;top:151px;width:1200px;height:501px}
.hero-photo{position:absolute;inset:0;background:radial-gradient(ellipse at 60% 45%,#6d6b68 0%,#3f3d3b 45%,#1e1d1c 100%)}
.hero-photo::after{content:"";position:absolute;inset:0;background:rgba(0,0,0,.35)}
.hero-title{position:absolute;left:0;width:1200px;top:174px;text-align:center;font-family:"Montserrat",Arial,sans-serif;font-weight:600;font-size:37px;letter-spacing:1px;color:var(--white)}
.hero-text{position:absolute;left:305px;width:590px;top:246px;text-align:center;font-size:12px;line-height:26px;color:var(--white)}
.btn{display:flex;align-items:center;justify-content:center;font-family:"Montserrat",Arial,sans-serif;font-weight:600;color:var(--white);letter-spacing:.5px}
.hero .btn{position:absolute;left:531px;top:349px;width:138px;height:40px;background:var(--green);font-size:14px}
.slider-arrow{position:absolute;top:224px;width:54px;height:54px;border:2px solid var(--white);border-radius:50%;display:flex;align-items:center;justify-content:center}
.slider-arrow.prev{left:23px}
.slider-arrow.next{left:1121px}

/* Section heads */
.section-title{position:absolute;left:0;width:1200px;text-align:center;font-family:"Montserrat",Arial,sans-serif;font-weight:500;font-size:23px;color:#4a4a4a;letter-spacing:.5px}
.section-sub{position:absolute;left:0;width:1200px;text-align:center;font-size:12px;color:var(--muted)}

/* How it works */
.how{position:absolute;left:0;top:652px;width:1200px;height:488px}
.how .section-title{top:46px}
.how .section-sub{top:93px}
.step{position:absolute;top:145px;width:340px;text-align:center}
.step-icon{position:relative;width:128px;height:128px;margin:0 auto;border:5px solid var(--green);border-radius:50%;display:flex;align-items:center;justify-content:center}
.step-num{position:absolute;left:48px;bottom:-16px;width:32px;height:32px;border-radius:50%;background:#555;color:var(--white);font-size:12px;display:flex;align-items:center;justify-content:center;border:3px solid var(--white)}
.step-name{margin-top:32px;font-family:"Montserrat",Arial,sans-serif;font-weight:600;font-size:16px;color:var(--green);letter-spacing:.5px}
.step-tag{margin-top:6px;font-size:12px;color:var(--muted);letter-spacing:.3px}
.step-text{margin:22px auto 0;width:290px;font-size:12px;line-height:24.5px;color:var(--text)}
.step-link{position:absolute;top:190px}

/* Pricing */
.prices{position:absolute;left:0;top:1140px;width:1200px;height:678px;background:var(--soft)}
.prices .section-title{top:36px}
.prices .section-sub{top:84px}
.plan{position:absolute;background:var(--white);border:1px solid #e2e4e6;border-radius:4px;box-shadow:0 2px 6px rgba(0,0,0,.06);text-align:center}
.plan-dot{position:absolute;left:50%;top:-14px;width:16px;height:16px;margin-left:-8px;border-radius:50%;background:#555;box-shadow:0 0 0 6px var(--soft)}
.plan-name{font-family:"Montserrat",Arial,sans-serif;font-weight:500;font-size:17px;color:#3f3f3f;letter-spacing:.5px;white-space:nowrap}
.plan-price{width:110px;height:110px;margin:0 auto;border-radius:50%;background:#555;color:var(--white);display:flex;align-items:center;justify-content:center;font-weight:700;font-size:26px}
.plan ul{list-style:none;margin:0 16px}
.plan li{height:43px;line-height:43px;font-size:12px;color:var(--text);border-bottom:1px solid var(--line);white-space:nowrap;overflow:hidden}
.plan .btn{margin:16px auto 0;width:116px;height:40px;background:#555;font-size:14px;border-radius:2px}
.plan.side{top:167px;width:258px;height:431px;padding-top:30px}
.plan.side .plan-name{margin-bottom:20px}
.plan.side ul{margin-top:26px;margin-left:10px;margin-right:10px}
.plan.featured{left:442px;top:144px;width:316px;height:478px;padding-top:53px;z-index:2}
.plan.featured .plan-dot{background:var(--green)}
.plan.featured .plan-name{margin-bottom:20px}
.plan.featured .plan-price{background:var(--green)}
.plan.featured ul{margin-top:39px}
.plan.featured .btn{background:var(--green)}

/* CTA band */
.cta{position:absolute;left:0;top:1818px;width:1200px;height:329px;overflow:hidden}
.cta-bg{position:absolute;inset:0}
.cta-title{position:absolute;font-family:"Montserrat",Arial,sans-serif;font-size:25px;color:var(--white);line-height:35px;letter-spacing:.5px}
.cta-title strong{font-weight:500}
.cta-title span{font-weight:400}
.cta-categories .cta-title{left:87px;top:59px}
.cta-categories p{position:absolute;left:87px;top:150px;width:480px;font-size:12px;line-height:30px;color:var(--white)}
.btn-outline{position:absolute;border:1px solid var(--white);font-size:15px}
.cta-categories .btn-outline{left:87px;top:228px;width:144px;height:44px}
.cta-newsletter .cta-title{left:662px;top:59px}
.email-field{position:absolute;left:664px;top:148px;width:437px;height:42px;background:var(--white);font-size:12px;color:#888;padding:0 12px;display:flex;align-items:center}
.cta-newsletter .btn-outline{left:665px;top:215px;width:143px;height:42px;font-size:14px}

/* Footer */
.site-footer{position:absolute;left:0;top:2147px;width:1200px;height:367px;background:var(--soft)}
.site-footer .brand{left:92px;top:86px;font-size:24px}
.social{position:absolute;left:104px;top:162px;display:flex;gap:6px}
.social span{width:36px;height:36px;border:1px solid #b8bcc0;border-radius:50%}
.footer-col{position:absolute;top:42px}
.footer-col h4{font-family:"Montserrat",Arial,sans-serif;font-weight:500;font-size:15px;color:#4a4a4a;letter-spacing:.5px}
.footer-col ul{list-style:none;margin-top:22px}
.footer-col li{font-size:12px;color:#666;height:30px;display:flex;align-items:center;gap:18px;padding-left:2px}
.footer-col li::before{content:"»";color:#888;font-size:12px}
.col-related{left:342px}
.col-compare{left:600px}
.col-social{left:857px}
.page-widget{position:absolute;left:0;top:38px;width:256px;height:200px;background:var(--white);border:1px solid #dcdfe2}
.widget-photo{position:absolute;left:0;top:0;width:254px;height:128px;background:linear-gradient(135deg,#6b7b8c 0%,#4a5562 50%,#8a6a4c 100%)}
.widget-name{position:absolute;left:64px;top:8px;font-weight:700;font-size:15px;color:var(--white)}
.widget-thumb{position:absolute;left:6px;top:8px;width:50px;height:50px;background:var(--white);border:1px solid #ccc}
.widget-btn{position:absolute;top:96px;height:24px;background:var(--white);border:1px solid #ccc;border-radius:2px;font-size:11px;font-weight:700;color:#4b4f56;display:flex;align-items:center;padding:0 8px}
.widget-note{position:absolute;left:10px;top:140px;font-size:11px;color:#4b4f56}
.footer-rule{position:absolute;left:87px;top:297px;width:1026px;border-top:1px solid #dadde0}
.copyright{position:absolute;left:0;width:1200px;top:321px;text-align:center;font-size:12px;color:#666}
</style>
</head>
<body>

<header class="site-header">
  <a class="brand" href="#"><span class="brand-mark"></span>Prisvaktposten</a>
  <div class="lang-select"><span class="flag"></span>English
    <svg width="12" height="8" viewBox="0 0 12 8"><path d="M1 1l5 5 5-5" fill="none" stroke="#333" stroke-width="2"/></svg>
  </div>
</header>

<nav class="main-nav">
  <ul>
    <li class="active" style="width:107px">HOME</li>
    <li style="width:98px">ABOUT US</li>
    <li style="width:142px">BROADBAND</li>
    <li style="width:76px">MMS</li>
    <li style="width:116px">CURRENT</li>
    <li style="width:202px">HOSTING &amp; DOMAINS</li>
    <li style="width:116px">RESIDENTIAL ALARM</li>
    <li style="width:188px">CONTACT US</li>
  </ul>
</nav>

<section class="hero">
  <div class="hero-photo" role="img" aria-label="Dark photo of hands using a phone beside a laptop"></div>
  <h1 class="hero-title">PRISVAKTPOSTEN</h1>
  <p class="hero-text">Prisvaktposten.no aims to help consumers find the best providers of services to the best prices. We examine the market and brings together the best in our lists, so you as a consumer can find great deals from reputable consumers find the best providers &nbsp;players quickly, easily and safely.</p>
  <a class="btn" href="#">READ MORE</a>
  <span class="slider-arrow prev"><svg width="16" height="20" viewBox="0 0 16 20"><path d="M12 2L4 10l8 8" fill="none" stroke="#fff" stroke-width="3"/></svg></span>
  <span class="slider-arrow next"><svg width="16" height="20" viewBox="0 0 16 20"><path d="M4 2l8 8-8 8" fill="none" stroke="#fff" stroke-width="3"/></svg></span>
</section>

<section class="how">
  <h2 class="section-title">HOW IT WORKS</h2>
  <p class="section-sub">We collect the most relevant information about the service in one place so that you learn the most important thing in a short time.</p>

  <div class="step" style="left:85px">
    <div class="step-icon">
      <svg width="46" height="54" viewBox="0 0 46 54" fill="none" stroke="#0fa67b" stroke-width="2.5"><rect x="3" y="3" width="40" height="48" rx="2"/><path d="M10 14h4M18 14h18M10 23h4M18 23h18M10 32h4M18 32h18M10 41h4M18 41h18"/></svg>
      <span class="step-num">01</span>
    </div>
    <h3 class="step-name">SELECT CATEGORY</h3>
    <p class="step-tag">READ MORE ABOUT THE SERVICE</p>
    <p class="step-text">We collect the most relevant information about the service in one place so that you learn the most important thing in a short time.</p>
  </div>

  <svg class="step-link" style="left:372px" width="100" height="40" viewBox="0 0 100 40"><path d="M4 26C30 44 60 40 88 14" fill="none" stroke="#888" stroke-width="1.5" stroke-dasharray="2 4"/><path d="M80 12l12-2-4 11z" fill="#888"/></svg>

  <div class="step" style="left:430px">
    <div class="step-icon">
      <svg width="52" height="44" viewBox="0 0 52 44" fill="none" stroke="#0fa67b" stroke-width="3.5" stroke-linecap="round" stroke-linejoin="round"><path d="M4 12h42M36 3l10 9-10 9M48 32H6M16 23l-10 9 10 9"/></svg>
      <span class="step-num">02</span>
    </div>
    <h3 class="step-name">COMPARE PROVIDERS</h3>
    <p class="step-tag">CHOOSE AMONG THE BEST AND MOST RELIABLE.</p>
    <p class="step-text">We collect the most relevant information about the service in one place so that you learn the most important thing in a short time.</p>
  </div>

  <svg class="step-link" style="left:716px" width="100" height="40" viewBox="0 0 100 40"><path d="M4 26C30 44 60 40 88 14" fill="none" stroke="#888" stroke-width="1.5" stroke-dasharray="2 4"/><path d="M80 12l12-2-4 11z" fill="#888"/></svg>

  <div class="step" style="left:775px">
    <div class="step-icon">
      <svg width="66" height="62" viewBox="0 0 66 62" fill="none" stroke="#0fa67b" stroke-width="4"><circle cx="24" cy="24" r="12"/><circle cx="24" cy="24" r="4"/><path d="M24 4v6M24 38v6M4 24h6M38 24h6M10 10l4 4M34 34l4 4M10 38l4-4M34 14l4-4"/><circle cx="48" cy="46" r="8"/><path d="M48 33v4M48 55v4M35 46h4M57 46h4"/></svg>
      <span class="step-num">03</span>
    </div>
    <h3 class="step-name">ORDER SERVICE</h3>
    <p class="step-tag">ORDER THE BEST SUPPLIER</p>
    <p class="step-text">We collect the most relevant information about the service in one place so that you learn the most important thing in a short time.</p>
  </div>
</section>

<section class="prices">
  <h2 class="section-title">OUR COMPARE PRICES</h2>
  <p class="section-sub">We collect the most relevant information about the service in one place so that you learn the most important thing in a short time.</p>

  <div class="plan side" style="left:188px">
    <span class="plan-dot"></span>
    <h3 class="plan-name">ELECTRICITY PLAN</h3>
    <div class="plan-price">$7.99</div>
    <ul><li>Power prices have increased during the</li><li>Decades, and there are various reasons</li><li>On the other hand, international</li><li>Events also led to electricity prices</li></ul>
    <a class="btn" href="#">COMPARE</a>
  </div>

  <div class="plan featured">
    <span class="plan-dot"></span>
    <h3 class="plan-name">MOBILE PLANS</h3>
    <div class="plan-price">$20.97</div>
    <ul><li>Power prices have increased during the</li><li>Decades, and there are various reasons</li><li>On the other hand, international</li><li>Events also led to electricity prices</li></ul>
    <a class="btn" href="#">COMPARE</a>
  </div>

  <div class="plan side" style="left:758px">
    <span class="plan-dot"></span>
    <h3 class="plan-name">BROADBAND PLAN</h3>
    <div class="plan-price">$25.96</div>
    <ul><li>Power prices have increased during the</li><li>Decades, and there are various reasons</li><li>On the other hand, international</li><li>Events also led to electricity prices</li></ul>
    <a class="btn" href="#">COMPARE</a>
  </div>
</section>

<section class="cta">
  <svg class="cta-bg" width="1200" height="329" viewBox="0 0 1200 329"><rect width="1200" height="329" fill="#4e4e4e"/><polygon points="0,0 637,0 570,329 0,329" fill="#0fa67b"/></svg>
  <div class="cta-categories">
    <h2 class="cta-title"><strong>LOOK THROUGH</strong><br><span>THE AVAILABLE CATEGORIES</span></h2>
    <p>Begin to investigate and compare the providers of the services you need.The best and most reputable players compared so you can choose ....</p>
    <a class="btn btn-outline" href="#">START NOW!</a>
  </div>
  <div class="cta-newsletter">
    <h2 class="cta-title"><strong>SUBSCRIBE TO</strong><br><span>OUR NEWSLETTER</span></h2>
    <div class="email-field">Enter Your Email Id :</div>
    <a class="btn btn-outline" href="#">SUBSCRIBE</a>
  </div>
</section>

<footer class="site-footer">
  <a class="brand" href="#"><span class="brand-mark"></span>Prisvaktposten</a>
  <div class="social"><span></span><span></span><span></span><span></span><span></span></div>

  <div class="footer-col col-related">
    <h4>RELATED PAGES</h4>
    <ul><li>Home</li><li>About us</li><li>Contact</li><li>Terms</li><li>Privacy</li><li>Cookies</li></ul>
  </div>
  <div class="footer-col col-compare">
    <h4>COMPARE SERVICES</h4>
    <ul><li>Cheap mms</li><li>Current</li><li>To me</li><li>Web hosting</li><li>Residential Alarm</li><li>Broadband</li></ul>
  </div>
  <div class="footer-col col-social">
    <h4>FIND US ON KRETSBOOK</h4>
    <div class="page-widget">
      <div class="widget-photo" role="img" aria-label="Cover photo of modern city buildings"></div>
      <span class="widget-thumb"></span>
      <span class="widget-name">Prisvaktposten</span>
      <span class="widget-btn" style="left:6px">Like Page</span>
      <span class="widget-btn" style="left:194px">Share</span>
      <p class="widget-note">Be the first of your friends to like this</p>
    </div>
  </div>

  <div class="footer-rule"></div>
  <p class="copyright">© Copyright 2017 Prisvaktposten .All Rights Reserved</p>
</footer>

</body>
</html>
```